Foot and ankle surgeon requires a website design

I need a website where prospective and established patients can obtain information and then direct them to making appointments. My practice is a highly professional surgical practice specialising in surgery to the foot and ankle. My title is Mr Colin Brasket, Podiatric Foot & Ankle Surgeon. My qualifications are: BSc MSc FACPS
The practice website will require information on: Locations, phone numbers to make appointments, general background on podiatric surgery,
I would like to include information on: my hospital appointments, surgical fellowships held, training programs undertaken, association memberships, publications written, links to useful websites
A page dedicated to common foot conditions would be useful and also a page with referral information including an online registration section that will be sent direct to the receptionist.
Examples of similar websites include:
http://www.dorvelquintaro.com.au/
http://www.haldenfootsurgeon.com.au/
I will provide files on logo, self photos and my personal training history etc.
Also if there is going to be a background theme I personally am associated with surfing and beach activities, it would be great if this was able to be reflected in the design.
Thank you.

```html
<!DOCTYPE html>
<html lang="en">
<head>
<meta charset="utf-8">
<title>Mr Colin Brasket – Podiatric Foot &amp; Ankle Surgeon</title>
<link href="https://fonts.googleapis.com/css2?family=Montserrat:wght@400;700&family=Open+Sans:wght@400;600;700&display=swap" rel="stylesheet">
<style>
:root{
  --orange:#f27420;
  --orange-dark:#d95f10;
  --blue:#1f4e8c;
  --page:#f2f1ef;
  --text:#222;
  --muted:#9a9a9a;
  --footer:#333334;
  --footer-deep:#1e1e1f;
  --footer-line:#444;
  --sand-1:#fdf3b0;
  --sand-2:#f6cf62;
}
*{box-sizing:border-box;margin:0;padding:0}
html,body{width:1200px;height:900px;overflow:hidden}
body{
  position:relative;
  font-family:"Open Sans",Arial,sans-serif;
  background:radial-gradient(ellipse at 50% 40%,var(--sand-1) 0%,#f9e68a 45%,var(--sand-2) 100%);
  color:var(--text);
}
.abs{position:absolute}
h2,h3,h4{font-family:"Montserrat",Arial,sans-serif}

/* header */
.brand{left:200px;top:6px;display:flex;align-items:center;gap:8px}
.brand-mark{width:44px;height:44px;border-radius:50%;background:var(--blue);opacity:.85}
.brand-name{font-family:"Montserrat",Arial,sans-serif;font-weight:700;font-size:14px;color:var(--blue);line-height:1.1;padding-top:18px}
.brand-tag{font-size:9px;font-weight:700;color:var(--orange);font-family:"Montserrat",Arial,sans-serif}
.social-top{left:668px;top:39px;display:flex;gap:8px}
.social-top span{width:19px;height:12px;background:#b7b19c;border-radius:2px;display:block}
.search{left:868px;top:39px;display:flex}
.search-field{width:121px;height:12px;background:#fff;border:1px solid #ddd;font-size:6px;color:#aaa;padding-left:4px;line-height:10px}
.search-btn{width:23px;height:12px;background:var(--orange);border-radius:0 2px 2px 0}

/* nav */
.nav{left:190px;top:66px;width:823px;height:21px;background:var(--orange);border-radius:3px 3px 0 0;display:flex;align-items:center;padding-left:13px}
.nav a{color:#fff;text-decoration:none;font-family:"Montserrat",Arial,sans-serif;font-size:9px;padding:1px 10px;margin-right:21px}
.nav a.active{border:1px solid #fff;border-radius:1px}

/* page */
.sheet{left:190px;top:87px;width:823px;height:640px;background:var(--page)}
.hero{left:190px;top:87px;width:823px;height:170px;background:linear-gradient(90deg,#d8d6d2 0%,#e9ecf0 35%,#a9c6e8 60%,#f4f5f6 100%)}
.hero-curve{left:190px;top:225px}
.dots{left:586px;top:260px;display:flex;gap:3px}
.dots i{width:5px;height:5px;border-radius:50%;background:#999}
.dots i:first-child{background:var(--orange)}
.intro h2{font-size:15px;font-weight:700;color:#222}
.intro p{font-size:7.5px;color:var(--muted);margin-top:1px;font-family:"Montserrat",Arial,sans-serif}
.btn{display:block;background:var(--orange);color:#fff;font-family:"Montserrat",Arial,sans-serif;text-align:center;border:1px solid var(--orange-dark);box-shadow:0 1px 2px rgba(0,0,0,.3)}
.btn-lg{left:839px;top:270px;width:143px;height:18px;font-size:11px;line-height:16px;letter-spacing:.5px}
.rule{left:205px;width:800px;height:1px;background:#e2e1de}

.feature{width:235px}
.feature h3{font-size:10px;font-weight:700;display:flex;align-items:center;gap:10px;margin-bottom:6px}
.feature p{font-family:"Montserrat",Arial,sans-serif;font-size:7.5px;line-height:9.6px;color:var(--muted);text-align:justify}

/* request form */
.request{left:750px;top:323px;width:282px;height:169px;background:var(--orange);border-radius:2px;box-shadow:0 2px 4px rgba(0,0,0,.35);padding:8px 20px 0 20px;color:#fff}
.request h3{font-size:11px;font-weight:700;display:flex;align-items:center;gap:10px;border-bottom:1px solid rgba(255,255,255,.4);padding-bottom:4px;margin-bottom:4px}
.request label{display:block;font-size:6px;margin-top:2px}
.field{background:#fff;height:11px;border:1px solid #e7e7e7;font-size:7px;color:#555;padding-left:3px;line-height:10px}
.field-row{display:flex;gap:4px}
.field-row .field{flex:1}
.field-area{height:43px}
.request-btn{margin-top:3px;width:107px;height:11px;background:#f2f2f2;color:#222;font-size:7px;font-weight:700;text-align:center;line-height:11px}

/* cards */
.card{width:173px}
.card h4{font-size:11px;font-weight:700;margin-bottom:5px}
.card-photo{height:59px;border-radius:3px;box-shadow:0 1px 3px rgba(0,0,0,.25)}
.card p{font-family:"Montserrat",Arial,sans-serif;font-size:7.5px;line-height:8.4px;color:var(--muted);text-align:justify;margin-top:4px}
.btn-sm{width:73px;height:11px;font-size:7px;line-height:9px;margin-top:6px}

.partners{left:218px;top:671px;width:768px;height:17px;background:#fff;border:1px solid #e6e6e6;display:flex;align-items:center;padding:0 20px;justify-content:space-between}
.partners .arrow{color:#ccc;font-size:10px}
.partners span{font-family:"Montserrat",Arial,sans-serif;font-weight:700;font-size:11px;color:#555;width:90px;text-align:center}

/* footer */
.footer{left:190px;top:703px;width:823px;height:197px;background:var(--footer)}
.footer-curve{left:190px;top:700px}
footer h4{font-size:10px;font-weight:700;color:#fff;border-bottom:1px solid #555;padding-bottom:4px;margin-bottom:4px;line-height:12px}
.foot-brand{left:215px;top:722px;display:flex;align-items:center;gap:8px}
.foot-brand .brand-mark{width:36px;height:36px;background:#888}
.foot-brand .name{font-family:"Montserrat",Arial,sans-serif;font-size:11px;font-weight:700;color:#ccc}
.foot-brand .tag{font-size:6px;color:#aaa}
.address{left:215px;top:769px;width:172px;color:#fff;font-size:7px;line-height:8px}
.address p{margin-top:6px}
.contact-line{display:flex;align-items:center;gap:9px;margin-top:3px}
.comments{left:417px;top:738px;width:170px}
.comment{display:flex;gap:10px;border-bottom:1px solid var(--footer-line);height:20.5px;padding-top:2px;font-size:7px;line-height:7px;color:#fff;overflow:hidden}
.comment b,.post b{color:var(--orange);font-size:8px;font-weight:600;display:block;line-height:8px}
.bubble{width:14px;height:8px;background:#aaa;border-radius:2px;margin-top:5px;flex:none}
.posts{left:617px;top:738px;width:172px}
.post{display:flex;gap:5px;height:35px;padding-top:3px;border-bottom:1px solid var(--footer-line);font-size:7px;line-height:7px;color:#fff;overflow:hidden}
.thumb{width:52px;height:25px;flex:none;border-radius:2px}
.contact{left:817px;top:738px;width:170px;color:#aaa;font-size:6px;line-height:8px}
.contact .in{background:#232323;border:1px solid var(--footer-line);height:11px;margin:1px 0 3px;width:152px}
.contact .ta{height:42px;width:170px}
.send{width:52px;height:11px;background:#222;border:1px solid #555;color:#ccc;font-size:7px;text-align:center;line-height:9px;margin-top:3px}
.copyright{left:190px;top:884px;width:823px;height:16px;background:var(--footer-deep);color:#ddd;font-size:7px;text-align:center;line-height:15px}
</style>
</head>
<body>

<header>
  <div class="abs brand">
    <span class="brand-mark"></span>
    <div>
      <div class="brand-name">Mr Colin Brasket</div>
      <div class="brand-tag">Podiatric Foot &amp; Ankle Surgeon</div>
    </div>
  </div>
  <div class="abs social-top" aria-label="Social links"><span></span><span></span><span></span><span></span><span></span><span></span><span></span></div>
  <div class="abs search"><div class="search-field">Search...</div><div class="search-btn"></div></div>
  <nav class="abs nav">
    <a class="active" href="#">Home</a><a href="#">About us</a><a href="#">Medical Services</a><a href="#">Our Doctors</a><a href="#">Appointments</a><a href="#">Locations</a>
  </nav>
</header>

<main>
  <div class="abs sheet"></div>
  <div class="abs hero" role="img" aria-label="Surgeon in white coat with two smiling nurses in blue scrubs"></div>
  <svg class="abs hero-curve" width="823" height="40" viewBox="0 0 823 40"><path d="M0 40 L0 28 Q411 -20 823 28 L823 40 Z" fill="#f2f1ef"/></svg>
  <div class="abs dots"><i></i><i></i><i></i></div>

  <div class="abs intro" style="left:215px;top:266px">
    <h2>Lorem ipsum dolor sit amet</h2>
    <p>Lorem ipsum dolor sit amet, consectetur adipisicing elit, sed do eiusmod tempor incididunt.</p>
  </div>
  <a class="abs btn btn-lg">READ MORE</a>
  <div class="abs rule" style="top:305px"></div>

  <section class="abs feature" style="left:218px;top:321px">
    <h3><svg width="20" height="12"><rect x="1" y="2" width="18" height="9" fill="#666"/></svg>Lorem ipsum dolor sit amet</h3>
    <p>Lorem ipsum dolor sit amet, consectetur adipisicing elit, sed do eiusmod tempor incididunt ut labore et dolore magna aliqua. Ut enim ad minim veniam, quis nostrud exercitation ullamco laboris nisi ut aliquip ex ea commodo consequat. Duis aute irure dolor in reprehenderit.</p>
  </section>
  <section class="abs feature" style="left:485px;top:321px">
    <h3><svg width="22" height="12"><circle cx="11" cy="6" r="4.5" fill="none" stroke="#666" stroke-width="2"/></svg>Lorem ipsum dolor sit amet</h3>
    <p>Lorem ipsum dolor sit amet, consectetur adipisicing elit, sed do eiusmod tempor incididunt ut labore et dolore magna aliqua. Ut enim ad minim veniam, quis nostrud exercitation ullamco laboris nisi ut aliquip ex ea commodo consequat. Duis aute irure dolor in reprehenderit.</p>
  </section>
  <section class="abs feature" style="left:218px;top:415px">
    <h3><svg width="20" height="12"><rect x="6" y="1" width="8" height="10" rx="1" fill="none" stroke="#666" stroke-width="2"/></svg>Lorem ipsum dolor sit amet</h3>
    <p>Lorem ipsum dolor sit amet, consectetur adipisicing elit, sed do eiusmod tempor incididunt ut labore et dolore magna aliqua. Ut enim ad minim veniam, quis nostrud exercitation ullamco laboris nisi ut aliquip ex ea commodo consequat. Duis aute irure dolor in reprehenderit.</p>
  </section>
  <section class="abs feature" style="left:485px;top:415px">
    <h3><svg width="22" height="12"><rect x="1" y="3" width="14" height="8" fill="#666"/><rect x="5" y="1" width="14" height="8" fill="#888"/></svg>Lorem ipsum dolor sit amet</h3>
    <p>Lorem ipsum dolor sit amet, consectetur adipisicing elit, sed do eiusmod tempor incididunt ut labore et dolore magna aliqua. Ut enim ad minim veniam, quis nostrud exercitation ullamco laboris nisi ut aliquip ex ea commodo consequat. Duis aute irure dolor in reprehenderit.</p>
  </section>

  <form class="abs request">
    <h3><svg width="26" height="12"><rect x="2" y="2" width="20" height="9" fill="#c25510"/></svg>Request A Timeslot</h3>
    <label>Your Name *</label><div class="field"></div>
    <label>Your Phone Number *</label><div class="field"></div>
    <label>Date &amp; Time Requested *</label><div class="field-row"><div class="field">Date</div><div class="field">Time</div></div>
    <label>Additional Information</label><div class="field field-area"></div>
    <div class="request-btn">MAKE REQUEST</div>
  </form>

  <article class="abs card" style="left:215px;top:509px">
    <h4>Lorem ipsum</h4>
    <div class="card-photo" role="img" aria-label="Row of bare feet" style="background:linear-gradient(180deg,#f3f3f3,#e2c2ac 60%,#f5f5f5)"></div>
    <p>Lorem ipsum dolor sit amet, consectetur adipisicing elit, sed do eiusmod tempor incididunt ut labore et dolore</p>
    <a class="btn btn-sm">READ MORE</a>
  </article>
  <article class="abs card" style="left:416px;top:509px">
    <h4>Lorem ipsum</h4>
    <div class="card-photo" role="img" aria-label="Manicured hands with a pink flower" style="background:linear-gradient(135deg,#e8b98a,#f0cfb4 50%,#d9a57c)"></div>
    <p>Lorem ipsum dolor sit amet, consectetur adipisicing elit, sed do eiusmod tempor incididunt ut labore et dolore</p>
    <a class="btn btn-sm">READ MORE</a>
  </article>
  <article class="abs card" style="left:617px;top:509px">
    <h4>Lorem ipsum</h4>
    <div class="card-photo" role="img" aria-label="Therapist examining a patient's foot" style="background:linear-gradient(90deg,#1f7f86,#2b9ba0 45%,#d9b49a 70%,#f4f4f4)"></div>
    <p>Lorem ipsum dolor sit amet, consectetur adipisicing elit, sed do eiusmod tempor incididunt ut labore et dolore</p>
    <a class="btn btn-sm">READ MORE</a>
  </article>
  <article class="abs card" style="left:818px;top:509px">
    <h4>Lorem ipsum</h4>
    <div class="card-photo" role="img" aria-label="Close-up of bare feet on a pale floor" style="background:linear-gradient(90deg,#f7e4da,#f2c5ad 40%,#fbefe9)"></div>
    <p>Lorem ipsum dolor sit amet, consectetur adipisicing elit, sed do eiusmod tempor incididunt ut labore et dolore</p>
    <a class="btn btn-sm">READ MORE</a>
  </article>

  <div class="abs partners">
    <b class="arrow">◀</b><span>Shorebook</span><span>Wavechat</span><span>Reeflink</span><span>Shorebook</span><span>Wavechat</span><span>Reeflink</span><b class="arrow">▶</b>
  </div>
</main>

<footer>
  <div class="abs footer"></div>
  <svg class="abs footer-curve" width="823" height="26" viewBox="0 0 823 26"><path d="M0 0 L823 0 L823 6 Q411 34 0 6 Z" fill="#f2f1ef"/></svg>

  <div class="abs foot-brand">
    <span class="brand-mark"></span>
    <div><div class="name">Mr Colin Brasket</div><div class="tag">Podiatric Foot &amp; Ankle Surgeon</div></div>
  </div>
  <div class="abs address">
    <h4>Address</h4>
    <p>Mr Colin Brasket<br>M.Sc, B.Sc, F.A.C.P.S.<br>PODIATRIC FOOT &amp; ANKLE SURGEON</p>
    <p style="margin-top:10px"></p>
    <div class="contact-line"><svg width="10" height="8"><path d="M1 2 Q1 0 3 0 L4 2 L3 3 Q4 5 6 6 L7 5 L9 6 Q9 8 7 8 Q1 7 1 2Z" fill="#f27420"/></svg>08 9470 2218</div>
    <div class="contact-line"><svg width="10" height="8"><rect x="1" y="1" width="8" height="6" fill="none" stroke="#f27420"/><path d="M1 1 L5 4 L9 1" fill="none" stroke="#f27420"/></svg>reception@cbfootcare.com.au</div>
    <div class="contact-line"><svg width="10" height="8"><path d="M5 8 L2 4 A3 3 0 1 1 8 4 Z" fill="#f27420"/></svg>www.cbfootcare.com.au</div>
  </div>

  <section class="abs comments">
    <h4>Latest Comments</h4>
    <div class="comment"><span class="bubble"></span><div><b>Mr Colin Brasket</b>Lorem ipsum dolor sit amet,<br>consectetur</div></div>
    <div class="comment"><span class="bubble"></span><div><b>Mr Colin Brasket</b>Lorem ipsum dolor sit amet,<br>consectetur</div></div>
    <div class="comment"><span class="bubble"></span><div><b>Mr Colin Brasket</b>Lorem ipsum dolor sit amet,<br>consectetur</div></div>
    <div class="comment"><span class="bubble"></span><div><b>Mr Colin Brasket</b>Lorem ipsum dolor sit amet,<br>consectetur</div></div>
    <div class="comment"><span class="bubble"></span><div><b>Mr Colin Brasket</b>Lorem ipsum dolor sit amet,<br>consectetur</div></div>
  </section>

  <section class="abs posts">
    <h4>Recent Posts</h4>
    <div class="post"><span class="thumb" role="img" aria-label="Foot massage" style="background:linear-gradient(90deg,#e7c3a8,#f2e6dc)"></span><div><b>Mr Colin Brasket</b>Lorem ipsum dolor sit amet,<br>consectetur<br>06-08-2014</div></div>
    <div class="post"><span class="thumb" role="img" aria-label="Foot joint diagram" style="background:linear-gradient(90deg,#f3f3f3,#e9cfc0)"></span><div><b>Mr Colin Brasket</b>Lorem ipsum dolor sit amet,<br>consectetur<br>06-08-2014</div></div>
    <div class="post"><span class="thumb" role="img" aria-label="Smiling patient" style="background:linear-gradient(90deg,#f4f4f4,#e3c0a3 50%,#f4f4f4)"></span><div><b>Mr Colin Brasket</b>Lorem ipsum dolor sit amet,<br>consectetur<br>06-08-2014</div></div>
  </section>

  <form class="abs contact">
    <h4>Contact Us</h4>
    <div>Your Name (required)</div><div class="in"></div>
    <div>Subject</div><div class="in"></div>
    <div>Your Message</div><div class="in ta"></div>
    <div class="send">SEND</div>
  </form>

  <div class="abs copyright">© 2014 Copyright, All Rights Reserved.</div>
</footer>

</body>
</html>
```